verdant terraces simple classy business card design

my name is colin barrow and I run a gardening business aimed at high class verdant terraces. the business name is verdant terraces and our logo was designed on pixel harbour .My clientel are anything from residential homes to businesses. I take pride in my work and know that I offer a service like no other in my area.
The business card will be used to represent my business and I want it to be not only rememberable, but simplistic and modern. Eye catching too. Of course I would like it relatable to gardening and appealing to the correct clientel - those being garden enthusiasts, prestigious homes and businesses that are after top of the line gardening services like no other on the market.
I am not a typical lawn mowing business so I don't want a typical card design that represents that. The gardens I work with are generally million dollar properties with owners who are very garden proud looking for upkeep and guidance from me along with sometimes whole new garden designs. I want the business cards to show to my clients that I take pride, as they do, in their garden. And I want them to know from my card that I am a professional, qualified horticulturist offering them a top of the line service for life. I want them to refer my business on. I want them to look at my business card and see class and professionalism in a modern unique bold way.
The card should be simple with the possibility of the logo on the front being embossed/debossed and my details on the back the card should have a organic garden feel it's very important to me that it is absolutely perfect
I am also very open to ideas and suggestions so look forward to seeing the designs. the business logo has been supplied with this project and I want the card to be double sided

Contact info is
Colin Barrow - Managing Director / Horticulturist
Phone : 0481 526 704
Email: colinbarrow@verdantterraces.example.au

Target Market(s)

high class gardens residential and commercial

Industry/Entity Type

Gardener

Contact Information for Business Card

Contact info is
Phone : 0481 526 704

PLEASE MAKE CARD DOUBLE SIDED

Requirements
Must have
• organic simple classy modern feel
• must flow with the current logo that has been supplied with this project
• Double sided
• Must explain in a simple way that I deal with high end gardens and I'm a qualified horticulturist
Nice to have
• embossed debossed logo
Should not have
• shouldn't be to busy or cheap looking

```html
<!DOCTYPE html>
<html lang="en">
<head>
<meta charset="utf-8">
<title>Verdant Terraces – Business Card</title>
<link rel="stylesheet" href="https://fonts.googleapis.com/css2?family=Cormorant+Garamond:wght@400&family=Montserrat:wght@400;500&display=swap">
<style>
  :root {
    --stage: #e6e7e8;
    --card-white: #ffffff;
    --leaf-green: #5f9e5c;
    --emboss-grey: #a9abad;
    --card-shadow: rgba(0, 0, 0, 0.35);
  }
  * { margin: 0; padding: 0; box-sizing: border-box; }
  html, body {
    width: 1200px;
    height: 927px;
    overflow: hidden;
    background: var(--stage);
  }
  .stage {
    position: relative;
    width: 1200px;
    height: 927px;
    background: var(--stage);
  }
  .card {
    position: absolute;
    top: 86px;
    width: 430px;
    height: 754px;
    overflow: hidden;
    box-shadow: 8px 8px 10px var(--card-shadow);
  }
  .card--front {
    left: 152px;
    background: var(--card-white);
  }
  .card--back {
    left: 618px;
    background: var(--leaf-green);
  }
  .brand-name {
    position: absolute;
    left: 0;
    width: 100%;
    text-align: center;
    font-family: "Cormorant Garamond", serif;
    font-weight: 400;
    text-transform: uppercase;
    color: var(--emboss-grey);
    font-size: 40px;
    letter-spacing: 3px;
    line-height: 1.1;
  }
  .card--front .brand-name {
    top: 150px;
  }
  .card--back .brand-name {
    top: 330px;
    color: var(--card-white);
  }
  .contact-line {
    position: absolute;
    left: 0;
    width: 100%;
    text-align: center;
    font-family: "Montserrat", sans-serif;
    font-weight: 400;
    color: var(--leaf-green);
    line-height: 1;
    white-space: nowrap;
    transform: translateY(-50%);
  }
  .contact__name {
    top: 583px;
    font-size: 28px;
    font-weight: 500;
  }
  .contact__role {
    top: 612px;
    font-size: 18.5px;
  }
  .contact__icons {
    top: 640px;
    display: flex;
    justify-content: center;
    gap: 6px;
    height: 13px;
  }
  .contact__phone {
    top: 669px;
    font-size: 18px;
    letter-spacing: 0.5px;
  }
  .contact__email {
    top: 692px;
    font-size: 17.5px;
  }
  .card__band {
    position: absolute;
    left: 0;
    bottom: 0;
    width: 100%;
    height: 26px;
    background: var(--leaf-green);
  }
</style>
</head>
<body>
<main class="stage">
  <section class="card card--front" aria-label="Card front">
    <p class="brand-name">Verdant<br>Terraces</p>
    <h1 class="contact-line contact__name">Colin Barrow</h1>
    <p class="contact-line contact__role">Managing Director / Horticulturist</p>
    <div class="contact-line contact__icons" aria-hidden="true">
      <svg width="11" height="13" viewBox="0 0 11 13">
        <path d="M2.5 1 L4.5 1 L5 4 L3.6 4.8 Q4.5 7.8 6.6 9.4 L7.8 8.2 L10 9.4 L9.6 11.6 Q4 12 1.6 3 Z" fill="none" stroke="var(--leaf-green)" stroke-width="1.2" stroke-linejoin="round"/>
      </svg>
      <svg width="14" height="13" viewBox="0 0 14 13">
        <rect x="1" y="3" width="12" height="8" fill="none" stroke="var(--leaf-green)" stroke-width="1.2"/>
        <path d="M1 3 L7 8 L13 3" fill="none" stroke="var(--leaf-green)" stroke-width="1.2"/>
      </svg>
    </div>
    <p class="contact-line contact__phone">0481 526 704</p>
    <p class="contact-line contact__email">colinbarrow@verdantterraces.example.au</p>
    <div class="card__band"></div>
  </section>

  <section class="card card--back" aria-label="Card back">
    <p class="brand-name">Verdant<br>Terraces</p>
  </section>
</main>
</body>
</html>
```